RTavenor Business Cards & Letterhead

I have a logo but need a design for some new business cards. We are a Design-Build Firm that specializes in the design and construction of commercial projects.
the cards need to be professional. no cartoon stuff.
i would like to have the cards in AI format so I can update the card as needed. Logo is provided.
Our Address is: 4187 Marlowe Ct. Millbrook, Ohio 27614

```html
<!DOCTYPE html>
<html lang="en">
<head>
<meta charset="utf-8">
<title>RTavenor Business Card</title>
<link href="https://fonts.googleapis.com/css2?family=Roboto:wght@400;500;700&display=swap" rel="stylesheet">
<style>
  :root {
    --backdrop: #3c3c3c;
    --paper: #f6f6f7;
    --brand-blue: #0a6ea8;
    --brand-blue-dark: #005a8e;
    --brand-blue-light: #0a7bb6;
    --ink: #444446;
    --ink-soft: #77787a;
    --wordmark: #3d3e40;
    --rule: #b9babc;
  }
  * { margin: 0; padding: 0; box-sizing: border-box; }
  html, body {
    width: 1200px; height: 1200px; overflow: hidden;
    background: var(--backdrop);
    font-family: "Roboto", Arial, sans-serif;
  }
  .canvas { position: relative; width: 1200px; height: 1200px; }

  .card {
    position: absolute; left: 262px; width: 686px; height: 392px;
    border-radius: 18px; overflow: hidden;
  }

  /* Front */
  .card-front { top: 165px; background: var(--paper); }
  .card-front .base-band {
    position: absolute; left: 0; right: 0; bottom: 0; height: 16px;
    background: linear-gradient(90deg, var(--brand-blue-dark), var(--brand-blue-light) 50%, var(--brand-blue-dark));
  }
  .brand {
    position: absolute; left: 78px; top: 180px;
    display: flex; align-items: center; gap: 6px;
  }
  .brand-square { width: 30px; height: 30px; background: var(--brand-blue); }
  .brand-name {
    font-weight: 700; font-size: 40px; letter-spacing: -0.5px;
    color: var(--wordmark); line-height: 1;
  }
  .divider {
    position: absolute; left: 365px; top: 108px; width: 1px; height: 180px;
    background: var(--rule);
  }
  .contact { position: absolute; left: 385px; top: 104px; color: var(--ink); }
  .contact .person {
    font-weight: 500; font-size: 23px; color: var(--brand-blue); line-height: 1.15;
  }
  .contact .role { font-size: 16px; color: var(--ink-soft); margin-bottom: 9px; }
  .contact .address { font-size: 17px; line-height: 21px; margin-bottom: 5px; }
  .contact ul { list-style: none; }
  .contact li {
    display: flex; align-items: center; gap: 10px;
    font-size: 17px; line-height: 20.5px;
  }
  .contact li svg { width: 16px; height: 16px; fill: var(--brand-blue); flex: none; }

  /* Back */
  .card-back {
    top: 653px;
    background: radial-gradient(ellipse at 45% 40%, #0a7bb6 0%, #066aa3 45%, #005689 100%);
    display: flex; align-items: center; justify-content: center; gap: 14px;
  }
  .card-back .brand-square { width: 44px; height: 44px; background: #ffffff; }
  .card-back .brand-name { color: #ffffff; font-size: 58px; }
</style>
</head>
<body>
<main class="canvas">
  <section class="card card-front">
    <div class="brand">
      <span class="brand-square"></span>
      <span class="brand-name">RTAVENOR</span>
    </div>
    <div class="divider"></div>
    <div class="contact">
      <p class="person">Daniel Whitmore</p>
      <p class="role">Managing Director</p>
      <p class="address">4187 Marlowe Ct. Millbrook<br>Ohio 27614</p>
      <ul>
        <li><svg viewBox="0 0 16 16" aria-hidden="true"><path d="M3.6 1.2l2.3 2.6c.4.4.3 1-.1 1.4l-1.1 1c.8 1.6 2 2.9 3.6 3.7l1-1.1c.4-.4 1-.5 1.4-.1l2.6 2.3c.4.4.4 1 0 1.4l-1.3 1.3c-.6.6-1.6.8-2.4.4C5.7 12.7 3.3 10.3 1.8 6.4c-.3-.8-.2-1.8.4-2.4L2.2 1.2c.4-.4 1-.4 1.4 0z"/></svg>919-555-0142</li>
        <li><svg viewBox="0 0 16 16" aria-hidden="true"><path d="M4.5 0h7c.8 0 1.5.7 1.5 1.5v13c0 .8-.7 1.5-1.5 1.5h-7C3.7 16 3 15.3 3 14.5v-13C3 .7 3.7 0 4.5 0zM4.6 2v10.5h6.8V2H4.6zM8 13.3a.9.9 0 100 1.8.9.9 0 000-1.8z"/></svg>919-555-0187</li>
        <li><svg viewBox="0 0 16 16" aria-hidden="true"><path d="M1 3.5h14v9H1v-9zm1.6 1.2L8 8.7l5.4-4H2.6zm11.2 1.1L8 10.1 2.2 5.8v5.5h11.6V5.8z"/></svg>info@rtavenor.com</li>
        <li><svg viewBox="0 0 16 16" aria-hidden="true"><circle cx="8" cy="8" r="7.5"/><path fill="#fff" d="M5 3.5c1 .2 1.6 1 1.3 1.8-.3.9-1.6.8-1.8 1.8-.2.9.9 1.3.7 2.3-.2.8-1.1 1-1.7.6A5.2 5.2 0 015 3.5zm5 2c.8-.3 1.9.3 2 1.2.2 1.4-.6 3.2-1.9 3.8-.8.3-1.2-.6-.9-1.4.3-.9-.2-1.4-.4-2.2-.1-.6.5-1.2 1.2-1.4z"/></svg>www.rtavenor.com</li>
      </ul>
    </div>
    <div class="base-band"></div>
  </section>

  <section class="card card-back">
    <span class="brand-square"></span>
    <span class="brand-name">RTAVENOR</span>
  </section>
</main>
</body>
</html>
```